New iOS App design for Boston Startup

We are looking for a new app design for our iPhone app. The current app's design feels outdated and we like to add lots of new functionality and a new navigation as well. A complete overhaul therefore!
We want you to design 5 screens that will have changed the most. The complete wireframes of these 5 pages are attached in the requirements document.
Once the winning design is selected we will award the winner with the designing all other screens (40-50 screens based on the same design). This will be a separate project worth $1000. The winning designer can get more follow up work if both sides are happy about the cooperation.
We will give feedback as soon as the first screen has been uploaded for review. Final decision will be made only after all 5 screens are finished.
We hope you give it your best!
Note: will only communicate through PixelHarbor (no skype),
Updates
Reason: Want to give designers a chance to submit their designs as I understand from some, the deadline is too close.
I have raised the award and introduced a 2nd price as well to make it worth your time. I hope you give it your best shot.
Reason: A few of you have asked for an extension of the deadline as time is running out. I will extend by one day. Tell me if you need more.
Industry/Entity Type
Startup
Requirements
Must have
- At least 1 screen before we can give you feedback.
Nice to have
- multiple options of 1 screen to get to a desirable design

```html
<!DOCTYPE html>
<html lang="en">
<head>
<meta charset="utf-8">
<title>Menu Screen</title>
<link rel="stylesheet" href="https://fonts.googleapis.com/css2?family=Roboto:wght@400;500&display=swap">
<style>
  :root {
    --page-bg: #eef1f4;
    --blue-light: #3cb4e6;
    --blue: #2287d3;
    --blue-dark: #1c78c4;
    --tile: #ffffff;
    --ink: #1b1b1b;
    --tab-bg: #f7f7f7;
    --tab-ink: #6f6f6f;
    --status-ink: #ffffff;
  }
  * { box-sizing: border-box; margin: 0; padding: 0; }
  html, body {
    width: 1200px; height: 797px; overflow: hidden;
    background: var(--page-bg);
    font-family: "Roboto", Helvetica, Arial, sans-serif;
  }
  .screen {
    position: absolute; left: 400px; top: 28px;
    width: 400px; height: 740px;
    background: var(--blue);
    display: flex; flex-direction: column;
    box-shadow: 0 6px 24px rgba(0,0,0,0.12);
  }
  .status-bar {
    height: 22px; padding: 0 10px;
    display: flex; align-items: center; justify-content: space-between;
    color: var(--status-ink); font-size: 12px;
    background: linear-gradient(90deg, var(--blue-light), var(--blue));
  }
  .status-bar .carrier, .status-bar .power { display: flex; align-items: center; gap: 5px; }
  .app-header {
    height: 46px; position: relative;
    display: flex; align-items: center; justify-content: center;
    background: linear-gradient(90deg, var(--blue-light), var(--blue-dark));
    color: #fff; font-size: 20px; font-weight: 500;
  }
  .menu-toggle { position: absolute; left: 14px; top: 12px; }
  .menu-grid {
    flex: 1;
    display: grid; grid-template-columns: 1fr 1fr; grid-template-rows: repeat(4, 1fr);
    gap: 10px; padding: 10px;
  }
  .menu-tile {
    background: var(--tile);
    display: flex; flex-direction: column; align-items: center; justify-content: center;
    gap: 10px; text-align: center;
    color: var(--ink); font-size: 17px; line-height: 1.2;
  }
  .menu-tile svg { width: 44px; height: 44px; fill: none; stroke: var(--ink); stroke-width: 2; stroke-linejoin: round; stroke-linecap: round; }
  .tab-bar {
    height: 58px; background: var(--tab-bg);
    display: grid; grid-template-columns: repeat(5, 1fr);
  }
  .tab {
    display: flex; flex-direction: column; align-items: center; justify-content: center; gap: 3px;
    color: var(--tab-ink); font-size: 11px;
  }
  .tab svg { width: 28px; height: 26px; fill: var(--tab-ink); }
  .tab.is-active { color: var(--blue); }
  .tab.is-active svg { fill: var(--blue); }
</style>
</head>
<body>
  <main class="screen">
    <div class="status-bar">
      <span class="carrier">VELO
        <svg width="14" height="10" viewBox="0 0 14 10" fill="none" stroke="#fff" stroke-width="1.6"><path d="M1 4a9 9 0 0 1 12 0M3.5 6.3a5.5 5.5 0 0 1 7 0"/><circle cx="7" cy="8.6" r="1" fill="#fff"/></svg>
      </span>
      <span class="clock">4:21 PM</span>
      <span class="power">
        <svg width="7" height="11" viewBox="0 0 7 11" fill="none" stroke="#fff" stroke-width="1.2"><path d="M1 3l5 5-2.5 2.5V.5L6 3 1 8"/></svg>
        100%
        <svg width="24" height="11" viewBox="0 0 24 11"><rect x="0.5" y="0.5" width="21" height="10" rx="2" fill="none" stroke="#fff"/><rect x="2" y="2" width="18" height="7" rx="1" fill="#fff"/><rect x="22" y="3.5" width="1.5" height="4" fill="#fff"/></svg>
      </span>
    </div>

    <header class="app-header">
      <svg class="menu-toggle" width="24" height="22" viewBox="0 0 24 22" fill="#fff"><rect y="1" width="24" height="3" rx="1.5"/><rect y="9.5" width="24" height="3" rx="1.5"/><rect y="18" width="24" height="3" rx="1.5"/></svg>
      Menu
    </header>

    <nav class="menu-grid">
      <a class="menu-tile">
        <svg viewBox="0 0 44 44"><path d="M4 14l18-8 18 8-18 8z"/><path d="M12 18v9c0 4 20 4 20 0v-9"/><path d="M40 14v10"/></svg>
        Profile
      </a>
      <a class="menu-tile">
        <svg viewBox="0 0 44 44"><path d="M22 6c6 0 8 5 7 10-1 4-3 7-7 7s-6-3-7-7c-1-5 1-10 7-10z"/><path d="M6 40c1-9 7-13 12-14M38 40c-1-9-7-13-12-14M6 40h32"/></svg>
        My Tutor
      </a>
      <a class="menu-tile">
        <svg viewBox="0 0 44 44"><path d="M17 4h10v28l-5 8-5-8z"/><path d="M17 10h10M17 32h10"/></svg>
        Advanced Writing<br>Assignment(AWA)
      </a>
      <a class="menu-tile">
        <svg viewBox="0 0 44 44"><path d="M6 20h7v18H6zM13 22l6-8 2-9c3 0 5 3 4 8l-1 4h12c2 0 3 2 2 4l-3 14c-1 2-2 3-4 3H13"/></svg>
        Social
      </a>
      <a class="menu-tile">
        <svg viewBox="0 0 44 44"><path d="M22 5c10 0 17 6 17 14s-7 14-17 14c-2 0-4 0-6-1l-8 5 2-7c-3-3-5-7-5-11C5 11 12 5 22 5z"/><path d="M18 15c0-3 8-3 8 1 0 3-4 3-4 6"/><circle cx="22" cy="26" r="0.8"/></svg>
        Vocabulary
      </a>
      <a class="menu-tile">
        <svg viewBox="0 0 44 44"><circle cx="22" cy="22" r="17"/><ellipse cx="22" cy="22" rx="8" ry="17"/><path d="M5 22h34M8 13h28M8 31h28M22 5v34"/></svg>
        Marketplace
      </a>
      <a class="menu-tile">
        <svg viewBox="0 0 44 44"><circle cx="22" cy="22" r="6"/><path d="M19 4h6l1 5 4 2 4-3 4 4-3 4 2 4 5 1v6l-5 1-2 4 3 4-4 4-4-3-4 2-1 5h-6l-1-5-4-2-4 3-4-4 3-4-2-4-5-1v-6l5-1 2-4-3-4 4-4 4 3 4-2z"/></svg>
        Settings
      </a>
      <a class="menu-tile">
        <svg viewBox="0 0 44 44"><circle cx="22" cy="22" r="17"/><path d="M22 19v12"/><circle cx="22" cy="13" r="1"/></svg>
        About the Nexora Exam
      </a>
    </nav>

    <footer class="tab-bar">
      <a class="tab">
        <svg viewBox="0 0 28 26"><path d="M14 2L2 13h4v11h6v-7h4v7h6V13h4z"/></svg>
        Home
      </a>
      <a class="tab">
        <svg viewBox="0 0 28 26" fill="none"><path d="M2 5c4-2 8-2 12 1 4-3 8-3 12-1v17c-4-2-8-2-12 1-4-3-8-3-12-1zM14 6v17" fill="none" stroke="#6f6f6f" stroke-width="1.6"/></svg>
        Theory
      </a>
      <a class="tab is-active">
        <svg viewBox="0 0 28 26"><path d="M14 1l10 5-10 5-10-5zM4 10l10 5 10-5v3l-10 5-10-5zM4 17l10 5 10-5v3l-10 5-10-5z"/></svg>
        Practice
      </a>
      <a class="tab">
        <svg viewBox="0 0 28 26"><path d="M7 7h14c4 0 6 5 6 10 0 4-3 5-5 2l-2-3H8l-2 3c-2 3-5 2-5-2 0-5 2-10 6-10z"/><rect x="6" y="11" width="5" height="1.6" fill="#fff"/><rect x="7.7" y="9.3" width="1.6" height="5" fill="#fff"/><circle cx="19" cy="10.5" r="1.2" fill="#fff"/><circle cx="21.5" cy="13" r="1.2" fill="#fff"/></svg>
        Games
      </a>
      <a class="tab">
        <svg viewBox="0 0 28 26"><path d="M8 21c-4 0-6-3-6-6s2-5 5-5c1-4 4-7 8-7 5 0 8 4 8 8 3 0 4 2 4 5s-2 5-5 5z"/><path d="M9 13l4 4 7-7" fill="none" stroke="#fff" stroke-width="2.2"/></svg>
        Test
      </a>
    </footer>
  </main>
</body>
</html>
```